business card - Helicopter Flight Services, Flight School, etc.

We need a business card design for a new helicopter service.

We offer Helicopter Flight Services, Aerial Filming & Photography, Flight School, and Helicopter Tours. In that order.

Summit BladeAir, Inc.
Dennis Tollerby
SummitBladeair@Kestmail.com
626-418-7352

Based at the Brenwick Airport in Van Nuys, CA. The final design should communicate integrity and safety. Pictures or logos at your discretion.

Card back side - surprise me.

```html
<!DOCTYPE html>
<html lang="en">
<head>
<meta charset="utf-8">
<title>Summit BladeAir, Inc. — Business Card</title>
<link rel="stylesheet" href="https://fonts.googleapis.com/css2?family=Open+Sans:wght@400;600;700&display=swap">
<style>
  :root {
    --bg: #e9ecef;
    --card: #ffffff;
    --blue-deep: #1273c4;
    --blue-mid: #2a93d8;
    --blue-light: #4fb3e6;
    --blue-pale: #8fd0f0;
    --ink-blue: #1a5aa6;
    --text-blue: #3a8fd6;
  }
  * { margin: 0; padding: 0; box-sizing: border-box; }
  html, body { width: 1200px; height: 913px; overflow: hidden; }
  body {
    background: var(--bg);
    font-family: "Open Sans", Arial, sans-serif;
    position: relative;
  }
  .card {
    position: absolute;
    top: 308px;
    width: 520px;
    height: 297px;
    background: var(--card);
    border-radius: 18px;
    overflow: hidden;
    box-shadow: 0 10px 28px rgba(0,0,0,0.18);
  }
  .card-front { left: 45px; }
  .card-back { left: 635px; }

  .front-wave { position: absolute; inset: 0; width: 100%; height: 100%; }

  .brand-front {
    position: absolute;
    top: 40px;
    right: 36px;
    display: flex;
    align-items: center;
    gap: 12px;
    color: #ffffff;
    font-weight: 700;
    font-size: 24px;
    letter-spacing: 0.5px;
  }
  .brand-dot {
    width: 16px; height: 16px;
    border-radius: 50%;
    background: #ffffff;
  }

  .contact {
    position: absolute;
    left: 30px;
    bottom: 24px;
    color: var(--text-blue);
  }
  .contact-name {
    font-weight: 700;
    font-size: 21px;
    color: var(--ink-blue);
    line-height: 1.15;
  }
  .contact-role {
    font-size: 14px;
    line-height: 1.3;
    margin-bottom: 8px;
    color: var(--text-blue);
  }
  .contact-line {
    display: flex;
    align-items: center;
    gap: 8px;
    font-size: 15px;
    line-height: 1.45;
  }
  .contact-line svg { width: 14px; height: 14px; flex: none; }

  .back-inner {
    position: absolute;
    inset: 0;
    display: flex;
    flex-direction: column;
    align-items: center;
    justify-content: center;
    gap: 26px;
  }
  .brand-back {
    display: flex;
    align-items: center;
    gap: 10px;
    color: var(--blue-mid);
    font-weight: 700;
    font-size: 24px;
  }
  .brand-back .brand-dot { background: var(--blue-mid); }
  .services {
    list-style: none;
    text-align: center;
    color: var(--text-blue);
    font-size: 16px;
    line-height: 1.35;
  }
</style>
</head>
<body>

<section class="card card-front" aria-label="Business card front">
  <svg class="front-wave" viewBox="0 0 520 297" preserveAspectRatio="none" aria-hidden="true">
    <defs>
      <linearGradient id="frontBlue" x1="0" y1="0" x2="1" y2="1">
        <stop offset="0" stop-color="#5cbde9"/>
        <stop offset="0.55" stop-color="#2a93d8"/>
        <stop offset="1" stop-color="#1273c4"/>
      </linearGradient>
    </defs>
    <path d="M0 0 H520 V80 C440 130 300 125 170 130 C90 134 30 138 0 145 Z" fill="url(#frontBlue)"/>
    <path d="M0 145 C30 138 90 134 170 130 C300 125 440 130 520 80 V90 C440 138 300 134 172 138 C92 142 32 146 0 153 Z" fill="var(--blue-pale)"/>
    <path d="M0 153 C32 146 92 142 172 138 C300 134 440 138 520 90 V96 C440 143 300 140 174 143 C94 147 34 151 0 158 Z" fill="#ffffff"/>
    <path d="M0 158 C34 151 94 147 174 143 C300 140 440 143 520 96 V102 C440 148 300 146 176 148 C96 152 36 156 0 163 Z" fill="var(--blue-light)"/>
  </svg>

  <div class="brand-front">
    <span class="brand-dot"></span>
    <span class="brand-name">Summit BladeAir, Inc.</span>
  </div>

  <div class="contact">
    <p class="contact-name">Dennis Tollerby</p>
    <p class="contact-role">Owner</p>
    <p class="contact-line">
      <svg viewBox="0 0 24 24" aria-hidden="true"><path fill="currentColor" d="M6.6 10.8a15 15 0 0 0 6.6 6.6l2.2-2.2c.3-.3.7-.4 1-.2 1.1.4 2.3.6 3.6.6.6 0 1 .4 1 1V20c0 .6-.4 1-1 1A17 17 0 0 1 3 4c0-.6.4-1 1-1h3.5c.6 0 1 .4 1 1 0 1.3.2 2.5.6 3.6.1.3 0 .7-.2 1z"/></svg>
      <span>626-418-7352</span>
    </p>
    <p class="contact-line">
      <svg viewBox="0 0 24 24" aria-hidden="true"><path fill="none" stroke="currentColor" stroke-width="2" d="M3 5h18v14H3z M3 5l9 8 9-8"/></svg>
      <span>SummitBladeair@Kestmail.com</span>
    </p>
  </div>
</section>

<section class="card card-back" aria-label="Business card back">
  <div class="back-inner">
    <div class="brand-back">
      <span class="brand-dot"></span>
      <span class="brand-name">Summit BladeAir, Inc.</span>
    </div>
    <ul class="services">
      <li>Aerial Filming &amp; Photography</li>
      <li>Flight School</li>
      <li>Helicopter Tours (In that order)</li>
    </ul>
  </div>
</section>

</body>
</html>
```